Brookvane Consulting Business Card Design

Business Card Design for Brookvane Consulting. Brookvane Consulting is a boutique consultancy based in Atlanta, GA., that specializes in marketing strategy, organization planning, and leadership development. We provide solutions for small businesses and startups as well as Vantage 300 companies.

http://brookvaneconsulting.com/

Target Market(s)

We provide solutions for small businesses and startups as well as Vantage 300 companies.

Industry/Entity Type

Consulting

Contact Information for Business Card

Two sided business card with priority on contact information, logo, tag line (Inspiration to Dream More, Do More, Become More)

Colors

Designer to choose colors to be used in the design.

Requirements
Must have
• contact information, logo, tag line (Inspiration to Dream More, Do More, Become More)
• Simple no over communication.
Nice to have
• I would like to see different placements of logo and creative use of both sides of the card
Should not have
• Do not put too much information on the card.

```html
<!DOCTYPE html>
<html lang="en">
<head>
<meta charset="utf-8">
<title>Brookvane Consulting Business Card</title>
<link href="https://fonts.googleapis.com/css2?family=Lato:wght@400;700&family=Norican&display=swap" rel="stylesheet">
<style>
  :root {
    --backdrop: #e4e2df;
    --card-black: #141414;
    --card-black-soft: #1f1f1f;
    --ink-white: #ffffff;
    --ink-grey: #b9b9b9;
    --band-grey: #a9a9a9;
    --band-text: #1a1a1a;
    --ornament-light: #e8e8e8;
  }
  * { margin: 0; padding: 0; box-sizing: border-box; }
  html, body { width: 1200px; height: 769px; overflow: hidden; }
  body {
    background: var(--backdrop);
    font-family: "Lato", sans-serif;
    position: relative;
  }
  .card {
    position: absolute;
    top: 230px;
    width: 540px;
    height: 309px;
    background: var(--card-black);
    border-radius: 4px;
    overflow: hidden;
    box-shadow: 0 10px 28px rgba(0,0,0,0.25);
  }
  .card--front { left: 40px; }
  .card--back { left: 620px; }

  /* Front side */
  .wordmark {
    position: absolute;
    color: var(--ink-white);
    font-family: "Lato", sans-serif;
    font-weight: 700;
    letter-spacing: 0.5px;
    white-space: nowrap;
  }
  .card--front .wordmark {
    top: 58px;
    right: 40px;
    font-size: 21px;
  }
  .holder-name {
    position: absolute;
    left: 40px;
    top: 104px;
    font-family: "Norican", cursive;
    font-size: 28px;
    color: var(--ink-grey);
  }
  .holder-title {
    position: absolute;
    left: 42px;
    top: 146px;
    font-size: 13px;
    color: var(--ink-white);
  }
  .contact-list {
    position: absolute;
    left: 42px;
    top: 188px;
    list-style: none;
  }
  .contact-list li {
    display: flex;
    align-items: center;
    gap: 9px;
    font-size: 12px;
    color: var(--ink-white);
    line-height: 18px;
  }
  .contact-list svg { width: 11px; height: 11px; fill: var(--ink-grey); }
  .tagline-band {
    position: absolute;
    left: 0;
    bottom: 22px;
    width: 100%;
    height: 26px;
    background: var(--band-grey);
    display: flex;
    align-items: center;
    padding-left: 42px;
    font-size: 12.5px;
    color: var(--band-text);
  }
  .tagline-ornament {
    position: absolute;
    right: 0;
    bottom: 48px;
    width: 170px;
    height: 30px;
    background: var(--ornament-light);
  }

  /* Back side */
  .back-pattern {
    position: absolute;
    inset: 0;
    background: linear-gradient(135deg, var(--card-black-soft), var(--card-black) 60%);
  }
  .card--back .wordmark {
    left: 50%;
    top: 50%;
    transform: translate(-50%, -50%);
    font-size: 32px;
  }
</style>
</head>
<body>
  <section class="card card--front" aria-label="Business card front">
    <div class="wordmark">Brookvane Consulting</div>
    <div class="holder-name">Darius Whitfield</div>
    <div class="holder-title">Founder/Managing Director</div>
    <ul class="contact-list">
      <li>
        <svg viewBox="0 0 24 24" aria-hidden="true"><path d="M6.6 10.8a15.1 15.1 0 0 0 6.6 6.6l2.2-2.2c.3-.3.7-.4 1-.2 1.1.4 2.3.6 3.6.6.6 0 1 .4 1 1V20c0 .6-.4 1-1 1A17 17 0 0 1 3 4c0-.6.4-1 1-1h3.5c.6 0 1 .4 1 1 0 1.3.2 2.5.6 3.6.1.3 0 .7-.2 1z"/></svg>
        555-014-2297
      </li>
      <li>
        <svg viewBox="0 0 24 24" aria-hidden="true"><path d="M2 5h20v14H2zm2 2v.5l8 5 8-5V7zm0 2.8V17h16V9.8l-8 5z"/></svg>
        darius@brookvaneconsulting.com
      </li>
      <li>
        <svg viewBox="0 0 24 24" aria-hidden="true"><circle cx="12" cy="12" r="10"/></svg>
        brookvaneconsulting.com
      </li>
    </ul>
    <div class="tagline-ornament" role="img" aria-label="Decorative geometric strip"></div>
    <div class="tagline-band">Inspiration to Dream More, Do More, Become More</div>
  </section>

  <section class="card card--back" aria-label="Business card back">
    <div class="back-pattern" role="img" aria-label="Subtle dark geometric background pattern"></div>
    <div class="wordmark">Brookvane Consulting</div>
  </section>
</body>
</html>
```